Need a clean & modern homepage for an education site + opportunity for longer term work

Thanks for viewing our project. We are excited about this new website and we hope that we might build a relationship with designers as we work on this project. I provided quite a few details and requirements to help you more quickly create a design that meets our needs.
Who we are:
We are a website that discusses the importance of college accreditation and provides a directory of college programs.
What we need:
A homepage that meets the below requirements and is inspired by the examples provided
Definition of accredited:
ac·cred·it·ed [uh-kred-i-tid] adj.
1. officially recognized as meeting the essential requirements, as of academic excellence: accredited schools.
2. provided with official credentials, as by a government: an accredited diplomatic representative.
3. accepted as authoritative: an accredited theory.
Overall look and feel for the homepage:
- Clean, simple and modern
- Limited (or zero) pictures
- Utilize color blocks with text
- A trend seems to be longer vertical length homepages with lots of whitespace. I generally like this trend as long as the page is not way to tall.
Inspirations: Sites that have a similar look and feel to what I need.
http://lernvoxa.org/
http://www.campusmetrik.com/colleges/brantmoor-university/
http://quietfolding.org/
http://www.velostrahiring.com/
http://www.zunq.com/
http://sketches.bxv.com/
Items to be included on the homepage. Details below on each item.
- Top navigation
- Logo: Please leave a blank area for a logo. The logo has not been designed.
- Simple graphic/color block at the top that highlights a definition of “Accredited” – the definition should be formatted like it is being copy/pasted from a dictionary.
- Space for a video and small (50 word) written description of the video. You can use placeholder text.
- One section with 3 Paragraphs of content (each paragraph around 100 words) with a header at the top. You can use placeholder text but please create the formatting. At the end of the 3 paragraphs please have a “Read More” Note this shouldn't be 3 separate paragraphs with three read mores - it is 3 paragraphs with one read more at the end.
- An area with the header “Search Colleges by State” that has anchor text links to all 50 states.
Top navigation:
- Home
- States – with a subnav dropdown that includes all 50 US states.
- Programs – with a subnav dropdown that includes program titles (list below)
- Degrees - with a subnav dropdown that includes 5 degree levels (list below)
- Accreditation – no subnav
- Rankings – no subnav
- Resources – no subnav
Footer
- Link to about us, privacy, and a copyright www.url.com
Programs List for sub navigation
Accounting
Art
Bible
Business
Criminal Justice
Design
Education
Engineering
English
Law
LPN to RN
Management
Math
MBA
MPH
Medical Assisting
Military
Nursing
Occupational Therapy
Paralegal
Psychology
Pharmacy
RN to BSN
Radiology
Social Work
Sonography
Degrees list for sub navigation
Certificate
Associate
Bachelors
Masters
PhD
Thanks so much - looking forward to working with you!
Education

```html
<!DOCTYPE html>
<html lang="en">
<head>
<meta charset="utf-8">
<title>My Website B\Name – Colleges &amp; Accreditation</title>
<link rel="stylesheet" href="https://fonts.googleapis.com/css2?family=Open+Sans:ital,wght@0,300;0,400;0,600;0,700;1,300;1,400;1,600&family=Caveat:wght@600&display=swap">
<style>
  :root {
    --blue: #1c74d6;
    --blue-deep: #1560bd;
    --navy: #1d3557;
    --nav-text: #5b7ea6;
    --orange: #f26522;
    --coral: #ee5b5b;
    --ink: #333333;
    --muted: #8a8a8a;
    --panel: #f3f3f3;
    --chip: #cfcfcf;
    --footer-bar: #c4c4c4;
    --yellow: #f5c400;
    --green: #34a56a;
    --royal: #2f6fd6;
    --white: #ffffff;
  }
  * { box-sizing: border-box; margin: 0; padding: 0; }
  html, body { width: 1200px; height: 2161px; overflow: hidden; }
  body { font-family: "Open Sans", Arial, sans-serif; color: var(--ink); background: var(--white); position: relative; }
  a { color: inherit; text-decoration: none; }

  /* Header */
  .site-header { position: relative; height: 84px; background: var(--white); }
  .site-name { position: absolute; left: 53px; top: 28px; font-size: 24px; font-weight: 400; color: var(--navy); letter-spacing: 0.5px; }
  .main-nav { position: absolute; right: 44px; top: 40px; display: flex; gap: 26px; font-size: 16px; color: var(--nav-text); }
  .main-nav .active { position: relative; }
  .main-nav .active::before { content: ""; position: absolute; left: 50%; top: -40px; width: 24px; height: 8px; margin-left: -12px; background: var(--blue); border-radius: 0 0 12px 12px; }
  .social { position: absolute; right: 52px; top: 6px; display: flex; gap: 10px; }
  .social span { width: 24px; height: 24px; border-radius: 50%; background: var(--blue); display: block; }

  /* Hero */
  .hero { position: relative; height: 446px; }
  .hero-pattern { position: absolute; inset: 0;
    background: linear-gradient(90deg, #e53d3d 0%, #f39b1d 14%, #4caf50 28%, #1c9ad6 42%, #ea3f7a 58%, #f5c400 72%, #31a862 86%, #e53d3d 100%); }
  .hero-card { position: absolute; left: 325px; top: 109px; width: 555px; height: 215px; background: var(--white); text-align: center; padding-top: 6px; }
  .hero-title { font-size: 30px; font-style: italic; font-weight: 400; line-height: 38px; color: var(--ink); }
  .hero-prompt { position: relative; margin-top: 4px; font-family: "Caveat", cursive; font-size: 30px; color: var(--ink); left: 58px; }
  .hero-prompt svg { position: absolute; right: 110px; top: -8px; }
  .search-bar { position: absolute; left: 12px; top: 158px; width: 518px; height: 48px; background: var(--blue); display: flex; align-items: center; padding: 6px; gap: 4px; }
  .search-field { height: 36px; background: var(--white); display: flex; align-items: center; padding: 0 14px; font-size: 15px; color: var(--muted); }
  .search-field.college { width: 234px; }
  .search-field.state { width: 136px; justify-content: space-between; }
  .search-button { flex: 1; height: 36px; background: var(--orange); color: var(--white); font-size: 18px; display: flex; align-items: center; justify-content: center; gap: 8px; }

  /* Video band */
  .video-band { position: relative; height: 230px; background: var(--blue); color: var(--white); }
  .video-copy { position: absolute; left: 125px; top: 34px; width: 470px; font-size: 15.5px; line-height: 19px; }
  .watch-button { position: absolute; left: 470px; top: 169px; width: 161px; height: 36px; border: 1.5px solid var(--white); font-size: 19px; display: flex; align-items: center; justify-content: center; }
  .watch-arrow { position: absolute; left: 640px; top: 158px; }
  .video-frame { position: absolute; left: 776px; top: 29px; width: 231px; height: 157px; background: linear-gradient(135deg, #e9eef4, #b9c8d8); box-shadow: 0 3px 8px rgba(0,0,0,0.25); }
  .play-mark { position: absolute; left: 50%; top: 50%; width: 48px; height: 48px; margin: -24px 0 0 -24px; border-radius: 50%; background: rgba(58,170,230,0.85); }
  .play-mark::after { content: ""; position: absolute; left: 19px; top: 14px; border-left: 15px solid var(--white); border-top: 10px solid transparent; border-bottom: 10px solid transparent; }

  /* Feature cards */
  .features { height: 360px; background: var(--panel); display: flex; justify-content: center; gap: 19px; padding-top: 28px; }
  .feature { width: 300px; text-align: center; }
  .feature-icon { width: 122px; height: 122px; border-radius: 50%; margin: 0 auto; }
  .feature-icon.yellow { background: var(--yellow); }
  .feature-icon.green { background: var(--green); }
  .feature-icon.royal { background: var(--royal); }
  .feature h2 { font-size: 31px; font-weight: 600; color: var(--navy); margin-top: 24px; line-height: 40px; }
  .feature p { margin: 14px auto 0; width: 290px; font-size: 12.5px; line-height: 14px; color: var(--muted); text-align: justify; height: 72px; overflow: hidden; }
  .read-more { display: inline-flex; align-items: center; justify-content: center; width: 170px; height: 43px; background: var(--coral); color: var(--white); font-size: 19px; }
  .feature .read-more { margin-top: 23px; }

  /* Content section */
  .content-section { position: relative; height: 446px; background: var(--white); border-top: 1px solid #e6e6e6; }
  .section-title { position: absolute; left: 137px; top: 58px; width: 300px; font-size: 45px; font-style: italic; line-height: 53px; }
  .section-title strong { font-weight: 400; }
  .section-title span { font-weight: 300; }
  .section-body { position: absolute; left: 453px; top: 50px; width: 628px; }
  .section-body h3 { font-size: 25px; font-style: italic; font-weight: 400; line-height: 30px; }
  .section-body p { font-size: 13.5px; line-height: 17px; color: var(--muted); text-align: justify; margin-bottom: 20px; }
  .content-section .read-more { position: absolute; left: 820px; top: 395px; }

  /* Directory */
  .directory { position: relative; height: 290px; background: var(--panel); }
  .directory h2 { position: absolute; top: 66px; font-size: 22px; font-weight: 700; color: var(--ink); }
  .directory h2.programs { left: 101px; }
  .directory h2.degrees { left: 660px; }
  .list-col { position: absolute; top: 108px; font-size: 14px; line-height: 17.5px; color: #555; list-style: none; padding-right: 30px; }
  .list-col.divided { border-left: 1px solid #9a9a9a; padding-left: 14px; }

  /* States */
  .states { position: relative; height: 228px; background: var(--white); }
  .states h2 { position: absolute; left: 101px; top: 30px; font-size: 24px; font-weight: 700; display: flex; align-items: center; gap: 8px; }
  .state-grid { position: absolute; left: 108px; top: 77px; display: grid; grid-template-columns: repeat(5, 125px); gap: 15px 17px; }
  .state-grid a { height: 26px; background: var(--chip); font-size: 14px; color: var(--ink); display: flex; align-items: center; justify-content: center; }
  .state-map { position: absolute; left: 810px; top: 24px; width: 280px; height: 180px; border-radius: 30px 60px 40px 70px; background: linear-gradient(135deg, #6d9ed6, #3b72bf); }

  /* Footer */
  .site-footer { position: relative; height: 77px; background: var(--footer-bar); color: #444; font-size: 26px; }
  .copyright { position: absolute; left: 116px; top: 18px; }
  .footer-links { position: absolute; left: 826px; top: 18px; display: flex; gap: 24px; }
</style>
</head>
<body>

<header class="site-header">
  <a class="site-name" href="#">MY WEBSITE B\NAME</a>
  <div class="social" aria-label="Social links"><span></span><span></span><span></span><span></span></div>
  <nav class="main-nav">
    <a class="active" href="#">Home</a>
    <a href="#">States</a>
    <a href="#">Programs</a>
    <a href="#">Degrees</a>
    <a href="#">Accreditation</a>
    <a href="#">Rankings</a>
    <a href="#">Resources</a>
  </nav>
</header>

<section class="hero">
  <div class="hero-pattern" role="img" aria-label="Colourful tiled pattern of school icons: pencils, books, apples, graduation caps, formulas"></div>
  <div class="hero-card">
    <p class="hero-title">Simple graphic/color block at the<br>top that highlights a definifrom a</p>
    <p class="hero-prompt">Serach your collage
      <svg width="40" height="46" viewBox="0 0 40 46" aria-hidden="true"><path d="M20 4 C34 8 34 26 22 38" fill="none" stroke="#333" stroke-width="2.5"/><path d="M16 30 L21 40 L30 34" fill="none" stroke="#333" stroke-width="2.5"/></svg>
    </p>
    <form class="search-bar">
      <div class="search-field college">Search Collage</div>
      <div class="search-field state">State
        <svg width="14" height="18" viewBox="0 0 14 18" aria-hidden="true"><path d="M7 1 C3.5 1 1 3.5 1 7 C1 11 7 17 7 17 C7 17 13 11 13 7 C13 3.5 10.5 1 7 1 Z" fill="none" stroke="#999" stroke-width="1.5"/><circle cx="7" cy="7" r="2" fill="#999"/></svg>
      </div>
      <div class="search-button">Search
        <svg width="18" height="18" viewBox="0 0 18 18" aria-hidden="true"><circle cx="7.5" cy="7.5" r="5.5" fill="none" stroke="#fff" stroke-width="2.5"/><path d="M11.5 11.5 L16.5 16.5" stroke="#fff" stroke-width="3"/></svg>
      </div>
    </form>
  </div>
</section>

<section class="video-band">
  <p class="video-copy">written description of the videowritten description of the videowritten description of the video written description of the video written description of the video written description of the video written&nbsp; description of the video written description of the videowritten description of the videowritten description of the video written description of the video written description of the video written description of the video written&nbsp; description of the video</p>
  <a class="watch-button" href="#">Watch video</a>
  <svg class="watch-arrow" width="120" height="50" viewBox="0 0 120 50" aria-hidden="true"><path d="M4 38 C30 50 70 44 104 12" fill="none" stroke="#fff" stroke-width="2.5"/><path d="M88 12 L106 10 L102 28" fill="none" stroke="#fff" stroke-width="2.5"/></svg>
  <div class="video-frame" role="img" aria-label="Video thumbnail of a smiling student"><span class="play-mark"></span></div>
</section>

<section class="features">
  <article class="feature">
    <div class="feature-icon yellow" role="img" aria-label="Graduate icon"></div>
    <h2>Ranking</h2>
    <p>One section with 3 Paragraphs of content (each paragraph around 100 words) with a header at the top. You can use placeholder text but please create the formatting. At the end of the 3 paragraphs please have a "Read</p>
    <a class="read-more" href="#">Read more</a>
  </article>
  <article class="feature">
    <div class="feature-icon green" role="img" aria-label="Graduation cap icon"></div>
    <h2>Accreditation</h2>
    <p>One section with 3 Paragraphs of content (each paragraph around 100 words) with a header at the top. You can use placeholder text but please create the formatting. At the end of the 3 paragraphs please have a "Read</p>
    <a class="read-more" href="#">Read more</a>
  </article>
  <article class="feature">
    <div class="feature-icon royal" role="img" aria-label="Graduation cap on book icon"></div>
    <h2>Resources</h2>
    <p>One section with 3 Paragraphs of content (each paragraph around 100 words) with a header at the top. You can use placeholder text but please create the formatting. At the end of the 3 paragraphs please have a "Read</p>
    <a class="read-more" href="#">Read more</a>
  </article>
</section>

<section class="content-section">
  <h2 class="section-title"><strong>Your section title&nbsp; here</strong><br><span>explain small-desc</span></h2>
  <div class="section-body">
    <h3>header at the top</h3>
    <p>One section with 3 Paragraphs of content (each paragraph around 100 words) with a header at the top. You can use placeholder text but please create the formatting. At the end of the 3 paragraphs please have a "Read More" Note this shouldn't be 3 separate paragraphs with three read mores - it is 3 paragraphs with one read more at the end.One section</p>
    <h3>header at the top</h3>
    <p>One section with 3 Paragraphs of content (each paragraph around 100 words) with a header at the top. You can use placeholder text but please create the formatting. At the end of the 3 paragraphs please have a "Read More" Note this shouldn't be 3 separate paragraphs with three read mores - it is 3 paragraphs with one read more at the end.One section</p>
    <h3>header at the top</h3>
    <p>One section with 3 Paragraphs of content (each paragraph around 100 words) with a header at the top. You can use placeholder text but please create the formatting. At the end of the 3 paragraphs please have a "Read More" Note this shouldn't be 3 separate paragraphs with three read mores - it is 3 paragraphs with one read more at the end.One section</p>
  </div>
  <a class="read-more" href="#">Read more</a>
</section>

<section class="directory">
  <h2 class="programs">Programs</h2>
  <h2 class="degrees">Degrees</h2>
  <ul class="list-col" style="left:104px"><li>Accounting</li><li>Art</li><li>Bible</li><li>Business</li><li>Criminal Justice</li><li>Design</li><li>Education</li><li>Engineering</li><li>English</li></ul>
  <ul class="list-col divided" style="left:292px"><li>Accounting</li><li>Art</li><li>Bible</li><li>Business</li><li>Criminal Justice</li><li>Design</li><li>Education</li><li>Engineering</li><li>English</li></ul>
  <ul class="list-col divided" style="left:470px;top:115px"><li>Accounting</li><li>Art</li><li>Bible</li><li>Business</li><li>Criminal Justice</li><li>Design</li><li>Education</li><li>Engineering</li><li>English</li></ul>
  <ul class="list-col divided" style="left:651px"><li>Accounting</li><li>Art</li><li>Bible</li><li>Business</li><li>Criminal Justice</li><li>Design</li><li>Education</li><li>Engineering</li><li>English</li></ul>
  <ul class="list-col divided" style="left:834px"><li>Accounting</li><li>Art</li><li>Bible</li><li>Business</li><li>Criminal Justice</li><li>Design</li><li>Education</li><li>Engineering</li><li>English</li></ul>
</section>

<section class="states">
  <h2><svg width="20" height="20" viewBox="0 0 20 20" aria-hidden="true"><circle cx="8" cy="8" r="6" fill="none" stroke="#555" stroke-width="2.5"/><path d="M12.5 12.5 L18 18" stroke="#555" stroke-width="3"/></svg>Colleges by State</h2>
  <nav class="state-grid">
    <a href="#">state</a><a href="#">state</a><a href="#">state</a><a href="#">state</a><a href="#">state</a>
    <a href="#">state</a><a href="#">state</a><a href="#">state</a><a href="#">state</a><a href="#">state</a>
    <a href="#">state</a><a href="#">state</a><a href="#">state</a><a href="#">state</a><a href="#">state</a>
  </nav>
  <div class="state-map" role="img" aria-label="Map of the United States divided into states"></div>
</section>

<footer class="site-footer">
  <p class="copyright">copyright@www.url.com</p>
  <nav class="footer-links"><a href="#">about us</a><a href="#">privacy</a></nav>
</footer>

</body>
</html>
```